Cover for a book about building companies without hierarchy

We need to design the cover of our new book. In 2018 we have developed a new organizational design called "Velmorith" which mean equal, just in Latin. This organizational design is hierarchy-free, and it is formed by a radial network of self-organizing teams, where people can take decisions pertaining their job, be autonomous, and contribute to the well being of the larger organization. We published a book in 2018 (see the cover attached), titled: "Velmorith. The Open People-first Structural Model to Flourish in a Shifting Era", where we used the graphic representation of the Velmorith structure in the cover (see attached). The book is intended for top managers, entrepreneurs, businesses.
After 5 years from its launch, we implemented this design in a number of companies and we learned a lot about what works and the challenges. So we decided to publish another book that will be titled: "Velmorith. 5 pillars to shape a people-first office" where we present a revised model, we focus on the principles behind Velmorith and we tell the story of the implementation of Velmorith in Corvellan Italy.
The book cover design must include both front and back, using the template attached.
In the front we need to include: an image or illustration, the Names of the authors (Marisa Tolvengo and Lorenzo Brucani) and the Pelvaro logo.
In the back we shall include: an empty space for the ISDN code as in the template, a short description of the book, the pictures and short bios of the authors .
In the spine we shall include: the title and authors.
Here's the bios:
Marisa Tolvengo is a partner at Pelvaro, a global organizational development firm, a former executive in the corporate setting (including Brindle & Moss and Quibbit! Inc.) and Past President of WPN Global (Worldwide Practitioner Network). She is the author of the book “Inner Compass. The Road to Renewing Guidance” and a FORAx speaker.
Lorenzo Brucani is a partner at Pelvaro and a former manager in multinational settings. He is the co-author of the Calloway Management Journal articles “Why Your Inner Climate Shapes your Output”, “3 Ways to Lift a Gloomy Day”, “Preparing Your Inner Climate for a Holiday Break” and “An Easy Method to Ease Lasting Tension”.
Pictures of the authors attached.
The final versions of the book cover shall be:
- book cover for paperback in English (front and back)
- Book cover for paperback in Italian (front and back)
- Book cover for kindle (only front)

```html
<!DOCTYPE html>
<html lang="en">
<head>
<meta charset="utf-8">
<title>Velmorith – Book Cover Wrap</title>
<link rel="stylesheet" href="https://fonts.googleapis.com/css2?family=Quicksand:wght@400;500;700&family=Saira+Semi+Condensed:wght@500&family=Saira+Extra+Condensed:wght@600&display=swap">
<style>
  :root {
    --page: #f3f3f2;
    --cover: #343333;
    --cream: #f7f1ea;
    --body: #e9e6e2;
    --name-yellow: #f4e97a;
    --gold-light: #f3d77a;
    --gold: #c9962e;
    --gold-deep: #8a6420;
    --photo-warm: #c98e78;
    --photo-cool: #a99a8e;
  }
  * { margin: 0; padding: 0; box-sizing: border-box; }
  html, body {
    width: 1200px; height: 1200px; overflow: hidden;
    background: var(--page);
  }
  .cover-wrap {
    position: absolute; left: 40px; top: 196px;
    width: 1120px; height: 808px;
    background: var(--cover);
    display: flex;
    box-shadow: 0 18px 40px rgba(0,0,0,0.25);
    font-family: "Quicksand", sans-serif;
    color: var(--body);
  }
  .back { position: relative; width: 540px; height: 100%; }
  .spine { position: relative; width: 42px; height: 100%; }
  .front { position: relative; width: 538px; height: 100%; }

  .gold-branches {
    position: absolute;
    background: radial-gradient(ellipse at center, rgba(243,215,122,0.55) 0%, rgba(201,150,46,0.35) 45%, rgba(52,51,51,0) 75%);
  }
  .back .gold-branches { left: 460px; top: 0; width: 80px; height: 390px; }
  .front .gold-branches { left: 0; top: 330px; width: 360px; height: 370px; }

  .blurb {
    position: absolute; left: 39px; top: 74px; width: 418px;
    font-size: 12.4px; line-height: 22px; font-weight: 500;
  }
  .blurb p + p { margin-top: 14px; }

  .bio {
    position: absolute; left: 39px; width: 470px;
    display: flex; gap: 14px;
  }
  .bio--first { top: 392px; }
  .bio--second { top: 550px; }
  .author-photo {
    flex: 0 0 86px; height: 122px;
    background: linear-gradient(160deg, var(--photo-cool), var(--photo-warm));
  }
  .bio-text { font-size: 11.2px; line-height: 23px; font-weight: 500; margin-top: -5px; }
  .bio-name { color: var(--name-yellow); font-weight: 700; }

  .spine-title {
    position: absolute; left: 50%; top: 62px; height: 690px;
    transform: translateX(-50%) rotate(180deg);
    writing-mode: vertical-rl;
    font-size: 11px; letter-spacing: 0.3px; white-space: nowrap;
    color: var(--cream); font-weight: 500;
    display: flex; justify-content: space-between;
  }
  .spine-title strong { font-weight: 700; }
  .spine-authors { font-family: "Saira Extra Condensed", sans-serif; font-size: 13px; letter-spacing: 0.6px; }

  .book-title {
    position: absolute; left: 0; right: 0; top: 72px;
    text-align: center;
    font-family: "Saira Semi Condensed", sans-serif; font-weight: 500;
    font-size: 104px; line-height: 1; color: var(--cream);
    letter-spacing: -1px;
  }
  .book-subtitle {
    position: absolute; left: 0; right: 0; top: 212px;
    text-align: center;
    font-family: "Saira Extra Condensed", sans-serif; font-weight: 600;
    font-size: 26px; line-height: 40px; letter-spacing: 2.2px;
    color: var(--cream);
  }
  .authors {
    position: absolute; left: 0; right: 0; top: 710px; padding-right: 8px;
    text-align: center; font-size: 16px; line-height: 29px;
    font-weight: 500; color: var(--cream); letter-spacing: 0.4px;
  }
  .publisher {
    position: absolute; right: 30px; top: 752px;
    font-size: 17px; font-weight: 700; letter-spacing: 1.5px;
    color: var(--cream);
  }
</style>
</head>
<body>
  <main class="cover-wrap">
    <section class="back">
      <div class="gold-branches" role="img" aria-label="Gold line illustration of branching leaf sprigs along the edge"></div>
      <div class="blurb">
        <p>Is your organization failing to create the environment where real collaboration, innovation and speed are a natural habit and people are truly engaged?</p>
        <p>What if the real key to all this was a radical change in the way your organization is actually structured?</p>
        <p>The authors’ 15+ year experience in change initiatives, together with the outcomes of an extensive qualitative and quantitative research, led to the creation of Velmorith. Velmorith is a revolutionary organizational model based on a radial and peer- based structure of self-organized and coordinated teams that overcome the limits of the hierarchy and expands individual, team and organizational potential.</p>
      </div>
      <div class="bio bio--first">
        <div class="author-photo" role="img" aria-label="Portrait photo of Marisa Tolvengo"></div>
        <p class="bio-text"><span class="bio-name">Marisa Tolvengo</span> is a partner at Pelvaro, a global organizational development firm, a former executive in the corporate setting (including Brindle &amp; Moss and Quibbit! Inc.) and Past President of WPN Global (Worldwide Practitioner Network). She is the author of the book “Inner Compass. The Road to Renewing Guidance” and a FORAx speaker.</p>
      </div>
      <div class="bio bio--second">
        <div class="author-photo" role="img" aria-label="Portrait photo of Lorenzo Brucani"></div>
        <p class="bio-text"><span class="bio-name">Lorenzo Brucani</span> is a partner at Pelvaro and a former manager in multinational settings. He is the co-author of the Calloway Management Journal articles “Why Your Inner Climate Shapes your Output”, “3 Ways to Lift a Gloomy Day”, “Preparing Your Inner Climate for a Holiday Break” and “An Easy Method to Ease Lasting Tension”.</p>
      </div>
    </section>

    <section class="spine">
      <p class="spine-title">
        <span><strong>Velmorith</strong> &nbsp;– 5 PILLARS TO SHAPE A PEOPLE-FIRST OFFICE</span>
        <span class="spine-authors">MARISA TOLVENGO - LORENZO BRUCANI</span>
      </p>
    </section>

    <section class="front">
      <h1 class="book-title">Velmorith</h1>
      <p class="book-subtitle">5 PILLARS TO SHAPE A<br>PEOPLE-FIRST OFFICE</p>
      <div class="gold-branches" role="img" aria-label="Gold line illustration of a radial network of leaf sprigs representing equal teams"></div>
      <p class="authors">MARISA TOLVENGO<br>&amp; LORENZO BRUCANI</p>
      <p class="publisher">PELVARO</p>
    </section>
  </main>
</body>
</html>
```